Need CATCHY/VIVID Banner design for my new UTV/ATV/Off Road Vehicle turn signal/lighting company

I need a banner ad designed so I can advertise on several different ATV (all terrain vehicle), UTV (Utility Vehicles), Golf Cart and Off-Road Vehicle forums. Ads need to be very catchy and produce a call to action. Action is getting hits to my website. Our main business is selling turn signal kits to make your side by side or your ATV/UTV street legal, as some states now allow you to drive these on public roads if you have the following items: Turn Signals, Horn, Lighted license plate bracket, headlights and brake lights. We sell all of these items for just about any model vehicle out there. Our call to action for this banner would be to get more website visits.

Target Market(s)

Off-road/outdoor enthusiasts,

Industry/Entity Type

Car Accessorie

Font styles to use
Sans Serif

Requirements
Must have
• Ad size need to be either 728x90 or 300x250. Colorful ad with an off-road vehicle integrated to the design (think UTV, side-by-side, etc.
Nice to have
• Nice to haves would be anything that makes this banner ad stand out on very boring web pages.
Should not have
• anything dull

```html
<!DOCTYPE html>
<html lang="en">
<head>
<meta charset="utf-8">
<title>Trailmark – ATV Vehicle Signal Lighting</title>
<link rel="stylesheet" href="https://fonts.googleapis.com/css2?family=Roboto:wght@300;400;700;900&display=swap">
<style>
  :root {
    --dark: #1a0709;
    --deep-red: #8e0f17;
    --red: #d3141d;
    --bright-red: #ee1c24;
    --yellow: #f7b500;
    --white: #ffffff;
    --machine-grey: #8d8b86;
    --machine-orange: #d2492a;
  }
  * { margin: 0; padding: 0; box-sizing: border-box; }
  html, body { width: 1200px; height: 148px; overflow: hidden; background: var(--dark); }
  .banner {
    position: relative;
    width: 1200px;
    height: 148px;
    overflow: hidden;
    font-family: "Roboto", Arial, sans-serif;
    color: var(--white);
    background: linear-gradient(90deg, var(--dark) 0%, #3a0b0f 16%, var(--deep-red) 30%, var(--red) 52%, var(--bright-red) 75%);
  }
  .backdrop-scene {
    position: absolute;
    left: 330px; top: 0;
    width: 520px; height: 148px;
    background: linear-gradient(180deg, rgba(255,255,255,0.10) 0%, rgba(255,255,255,0.04) 55%, rgba(0,0,0,0.08) 100%);
  }
  .accent-wedge {
    position: absolute; inset: 0;
    width: 1200px; height: 148px;
  }
  .brand {
    position: absolute;
    left: 24px; top: 0;
    width: 232px;
    text-align: center;
  }
  .brand-name {
    display: flex; align-items: center; justify-content: center; gap: 8px;
    margin-top: 30px;
    font-weight: 900; font-size: 26px; letter-spacing: 1px;
  }
  .brand-dot { width: 14px; height: 14px; border-radius: 50%; background: var(--white); }
  .brand-line-main {
    margin-top: 26px;
    font-weight: 700; font-size: 19px; letter-spacing: -0.2px; line-height: 1;
  }
  .brand-line-sub {
    margin-top: 4px;
    font-weight: 700; font-size: 13px; letter-spacing: 0.2px; line-height: 1;
  }
  .vehicle {
    position: absolute;
    border-radius: 18px;
  }
  .vehicle-left {
    left: 282px; top: 18px; width: 182px; height: 126px;
    background: radial-gradient(ellipse at 50% 55%, var(--machine-grey) 0%, #5a4b49 45%, rgba(40,20,20,0) 72%),
                radial-gradient(ellipse at 40% 25%, var(--machine-orange) 0%, rgba(210,73,42,0) 50%);
  }
  .vehicle-right {
    left: 830px; top: 20px; width: 330px; height: 128px;
    background: radial-gradient(ellipse at 50% 55%, var(--machine-grey) 0%, #4d4440 45%, rgba(40,30,20,0) 72%),
                radial-gradient(ellipse at 45% 20%, var(--machine-orange) 0%, rgba(210,73,42,0) 48%);
  }
  .headline {
    position: absolute;
    left: 476px; top: 22px; width: 300px;
    text-align: center;
  }
  .headline-top { font-weight: 300; font-size: 25px; line-height: 1; letter-spacing: 0.5px; }
  .headline-main { margin-top: 6px; font-weight: 700; font-size: 33px; line-height: 1; letter-spacing: 0.5px; }
  .feature-icons {
    position: absolute;
    left: 494px; top: 96px;
    display: flex; gap: 28px; align-items: center;
  }
  .feature-icons svg { display: block; }
</style>
</head>
<body>
<div class="banner">
  <div class="backdrop-scene" role="img" aria-label="Red-toned mountain landscape backdrop"></div>

  <svg class="accent-wedge" viewBox="0 0 1200 148" aria-hidden="true">
    <polygon points="920,0 1200,0 1200,148 832,148" fill="var(--yellow)"/>
  </svg>

  <div class="brand">
    <div class="brand-name"><span class="brand-dot"></span>TRAILMARK</div>
    <div class="brand-line-main">TURN SIGNAL KITS</div>
    <div class="brand-line-sub">&amp; LIGHTING ACCESSORIES</div>
  </div>

  <div class="vehicle vehicle-left" role="img" aria-label="Grey and orange side-by-side UTV"></div>

  <div class="headline">
    <div class="headline-top">ATV VECHICLE</div>
    <div class="headline-main">SIGNAL LIGHTING</div>
  </div>

  <div class="feature-icons">
    <svg width="32" height="28" viewBox="0 0 32 28" role="img" aria-label="Brake light">
      <circle cx="16" cy="14" r="9" fill="none" stroke="#fff" stroke-width="2.4"/>
      <rect x="14.8" y="8" width="2.4" height="8" fill="#fff"/>
      <rect x="14.8" y="18" width="2.4" height="2.4" fill="#fff"/>
      <path d="M5 5 A14 14 0 0 0 5 23 M27 5 A14 14 0 0 1 27 23" fill="none" stroke="#fff" stroke-width="2.4"/>
    </svg>
    <svg width="32" height="28" viewBox="0 0 32 28" role="img" aria-label="Headlight">
      <path d="M15 4 C5 4 3 9 3 14 C3 19 5 24 15 24 Z" fill="#fff"/>
      <g stroke="#fff" stroke-width="2.4"><line x1="19" y1="7" x2="30" y2="7"/><line x1="19" y1="12" x2="30" y2="12"/><line x1="19" y1="17" x2="30" y2="17"/><line x1="19" y1="22" x2="30" y2="22"/></g>
    </svg>
    <svg width="38" height="28" viewBox="0 0 38 28" role="img" aria-label="Horn">
      <path d="M4 12 L12 12 L30 4 L30 24 L12 16 L4 16 Z" fill="none" stroke="#fff" stroke-width="2.2" stroke-linejoin="round"/>
      <g stroke="#fff" stroke-width="2"><line x1="8" y1="8" x2="6" y2="3"/><line x1="13" y1="8" x2="13" y2="2"/><line x1="18" y1="8" x2="20" y2="3"/></g>
    </svg>
    <svg width="40" height="28" viewBox="0 0 40 28" role="img" aria-label="Turn signals">
      <path d="M2 14 L12 4 L12 10 L18 10 L18 18 L12 18 L12 24 Z" fill="none" stroke="#fff" stroke-width="2.2" stroke-linejoin="round"/>
      <path d="M38 14 L28 4 L28 10 L22 10 L22 18 L28 18 L28 24 Z" fill="none" stroke="#fff" stroke-width="2.2" stroke-linejoin="round"/>
    </svg>
    <svg width="20" height="30" viewBox="0 0 20 30" role="img" aria-label="Traffic light">
      <rect x="4" y="1" width="12" height="28" rx="3" fill="#fff"/>
      <g fill="var(--red)"><circle cx="10" cy="7" r="3"/><circle cx="10" cy="15" r="3"/><circle cx="10" cy="23" r="3"/></g>
      <g fill="#fff"><rect x="0" y="5" width="3" height="4"/><rect x="17" y="5" width="3" height="4"/><rect x="0" y="13" width="3" height="4"/><rect x="17" y="13" width="3" height="4"/></g>
    </svg>
  </div>

  <div class="vehicle vehicle-right" role="img" aria-label="Grey and orange two-seat UTV, front three-quarter view"></div>
</div>
</body>
</html>
```